Velvet Riot Rising Line of Sparkling Wine & Spirits

Back info: Nora Beth Quill Owner 555-318-4402 1480 E. Harlow Ave, Bldg. 2, & 3, Lodi Ca. 95871
Sparkling Wines & Memorabilia www.velvetriotrising.com
Ok I have uploaded the winning design. The color that I am after is the Fushia, Raspberry, Red, Matte Satin Matalic Finish. With a 24 Karet Gold color Foil. The Bottle is on the top row and it's the 2nd Bottle in. That is the Color that I want. This is the style of font. Make sure that you put what we're advertising. Good Luck to you all. Warmest regards, Nora
21 & up UniSex
Sparkling Wine and Memorabilia
there listed up above.....

```html
<!DOCTYPE html>
<html lang="en">
<head>
<meta charset="utf-8">
<title>Velvet Riot Rising – Business Card</title>
<link rel="stylesheet" href="https://fonts.googleapis.com/css2?family=Arimo:wght@400;700&display=swap">
<style>
  :root {
    --page: #e4e4e4;
    --card: #ffffff;
    --fuchsia: #d1146e;
    --fuchsia-deep: #a80d57;
    --fuchsia-light: #ec3d95;
    --gold: #e8b04a;
    --ink: #555555;
    --ink-dark: #222222;
    --rule: #9a9a9a;
  }
  * { box-sizing: border-box; margin: 0; padding: 0; }
  html, body {
    width: 1200px; height: 1200px; overflow: hidden;
    background: var(--page);
    font-family: "Arimo", Arial, sans-serif;
  }
  .canvas { position: relative; width: 1200px; height: 1200px; }
  .card {
    position: absolute; left: 140px;
    width: 920px; height: 526px;
    background: var(--card);
    box-shadow: 0 6px 18px rgba(0,0,0,0.18);
  }
  .card--front { top: 40px; }
  .card--back { top: 634px; }

  .bottle-art {
    position: absolute;
    border-radius: 40% 40% 14px 14px / 22% 22% 14px 14px;
    background: linear-gradient(90deg, var(--fuchsia-deep) 0%, var(--fuchsia-light) 45%, var(--fuchsia) 70%, var(--fuchsia-deep) 100%);
  }
  .card--front .bottle-art { left: 695px; top: 63px; width: 123px; height: 407px; }
  .card--back .bottle-art { left: 406px; top: 89px; width: 108px; height: 348px; }

  .contact { position: absolute; left: 87px; top: 224px; }
  .contact__name {
    font-size: 35px; font-weight: 700; color: var(--fuchsia);
    line-height: 1; letter-spacing: 0.2px;
  }
  .contact__role {
    font-size: 23px; color: var(--gold); line-height: 1.1; margin-top: 2px;
  }
  .contact__address {
    margin-top: 36px; font-size: 21px; color: var(--ink); line-height: 28px;
  }
  .contact__lines { margin-top: 28px; font-size: 21px; color: var(--ink); }
  .contact__line { display: flex; align-items: center; gap: 14px; line-height: 27px; }
  .contact__line svg { width: 19px; height: 19px; flex: none; }

  .back__rule {
    position: absolute; left: 176px; top: 437px; width: 608px; height: 1px;
    background: linear-gradient(90deg, transparent, var(--rule) 20%, var(--rule) 80%, transparent);
  }
  .back__tagline {
    position: absolute; left: 0; right: 0; top: 458px;
    text-align: center; font-size: 23px; letter-spacing: 0.22em;
    color: var(--ink-dark);
  }
  .back__tagline strong { color: var(--fuchsia); font-weight: 700; }
</style>
</head>
<body>
<div class="canvas">
  <section class="card card--front">
    <div class="contact">
      <h1 class="contact__name">NORA BETH QUILL</h1>
      <p class="contact__role">Owner</p>
      <p class="contact__address">E. Harlow Ave<br>Bldg. 2, &amp; 3, Lodi Ca. 95871</p>
      <div class="contact__lines">
        <p class="contact__line">
          <svg viewBox="0 0 24 24" aria-hidden="true"><path fill="var(--fuchsia)" d="M6.6 10.8a15.1 15.1 0 0 0 6.6 6.6l2.2-2.2a1 1 0 0 1 1-.25 11.4 11.4 0 0 0 3.6.57 1 1 0 0 1 1 1V20a1 1 0 0 1-1 1A17 17 0 0 1 3 4a1 1 0 0 1 1-1h3.5a1 1 0 0 1 1 1c0 1.25.2 2.45.57 3.57a1 1 0 0 1-.25 1z"/></svg>
          555-318-4402 1480
        </p>
        <p class="contact__line">
          <svg viewBox="0 0 24 24" aria-hidden="true"><circle cx="12" cy="12" r="10" fill="var(--fuchsia)"/><path d="M2 12h20M12 2c3 3 3 17 0 20M12 2c-3 3-3 17 0 20" stroke="#fff" stroke-width="1.4" fill="none"/></svg>
          www.velvetriotrising.com
        </p>
      </div>
    </div>
    <div class="bottle-art" role="img" aria-label="Fuchsia sparkling wine bottle with gold foil neck and Velvet Riot Rising label"></div>
  </section>

  <section class="card card--back">
    <div class="bottle-art" role="img" aria-label="Fuchsia sparkling wine bottle with gold foil neck and Velvet Riot Rising label"></div>
    <div class="back__rule"></div>
    <p class="back__tagline">SPARKLING <strong>WINES &amp; MEMORABILIA</strong></p>
  </section>
</div>
</body>
</html>
```